Tutoring Site Hero Image Design

Updated Hero Concept for BrightHarborLessons.com

Create a hero that communicates “high quality, in-person private tutoring for all ages,” with warmth, credibility, and a real-life feel. The hero should move away from generic stock photography and better reflect the moments that make our service different: tutors meeting students where they are, one-on-one engagement, and a range of ages.

What the New Hero Should Convey
1. In-person, private, one-on-one support
This is the core differentiator, so the visual should feel intimate, focused, and real. Avoid anything that resembles online learning settings or learning-center classrooms.

2. Coverage of age ranges without clutter
We serve elementary through college. We do not need multiple students in the hero, but the chosen student should not skew strongly to one age group. Aim for a middle-ground age that feels inclusive, for example a middle schooler or early high schooler.

3. Realistic, authentic moments
Use photography that feels candid and warm. Natural light, home settings, kitchen tables, quiet study nooks, or library corners work well. Avoid staged stock looks, harsh lighting, or exaggerated classroom setups.

Design the hero at 2400 × 1200 px, with the focal point on the right side, safe area leaving room on the left for a stacked headline and form.

Images that I've shared as just thought starters and do not need to be used in the design.

Font styles to use
Sans Serif

Colors
0054AA
0677BA
7BADD7
CADEEF
E8F1F8
EB3D1F
EC4F4E
F09395
F8D3D4
FCEDEE
6B429C
8869AF
B7A5CE
E3DAEB
F3F0F8

```html
<!DOCTYPE html>
<html lang="en">
<head>
<meta charset="utf-8">
<title>BrightHarborLessons.com – Local Tutors</title>
<link rel="stylesheet" href="https://fonts.googleapis.com/css2?family=Outfit:wght@400;500;600&family=Montserrat:wght@500&display=swap">
<style>
  :root {
    --navy: #001a70;
    --red: #e4002b;
    --white: #ffffff;
    --ink: #1a1a1a;
    --line: #9a9a9a;
    --photo-warm: #c89a6a;
    --photo-light: #e9e2cf;
    --photo-green: #8a9a6e;
  }
  * { box-sizing: border-box; margin: 0; padding: 0; }
  html, body { width: 1200px; height: 600px; overflow: hidden; }
  body { position: relative; background: var(--navy); font-family: "Outfit", sans-serif; }

  .hero-band { position: absolute; left: 0; top: 0; width: 262px; height: 600px; background: var(--navy); }
  .hero-photo {
    position: absolute; left: 262px; top: 0; width: 938px; height: 600px;
    background:
      radial-gradient(ellipse at 85% 25%, rgba(240,238,225,.95) 0%, rgba(220,225,205,.6) 35%, transparent 60%),
      radial-gradient(ellipse at 55% 45%, #b9825a 0%, transparent 45%),
      radial-gradient(ellipse at 80% 70%, #9fb3c8 0%, transparent 40%),
      linear-gradient(180deg, var(--photo-green) 0%, var(--photo-warm) 55%, var(--photo-light) 100%);
  }

  .headline {
    position: absolute; left: 49px; top: 38px;
    color: var(--white); font-weight: 500; font-size: 31px; letter-spacing: -0.3px; line-height: 1;
  }
  .headline-accent {
    position: absolute; left: 165px; top: 87px;
    color: var(--red); font-weight: 600; font-size: 31px; letter-spacing: -0.3px; line-height: 1;
  }

  .lead-form {
    position: absolute; left: 40px; top: 142px; width: 434px; height: 420px;
    background: var(--white); border-radius: 0 30px 30px 30px;
  }
  .field {
    position: absolute; height: 43px; border: 1px solid var(--line);
  }
  .field-label {
    position: absolute; left: 9px; top: -9px; padding: 0 4px;
    background: var(--white); color: var(--ink);
    font-family: "Montserrat", sans-serif; font-weight: 500; font-size: 12.5px; line-height: 16px;
    letter-spacing: .3px;
  }
  .field-caret { position: absolute; top: 18px; }
  .col-left { left: 20px; width: 188px; }
  .col-right { left: 225px; width: 188px; }
  .row-1 { top: 38px; }
  .row-2 { top: 113px; }
  .row-3 { top: 184px; }
  .field-message { left: 20px; top: 259px; width: 393px; height: 59px; }

  .submit-button {
    position: absolute; left: 103px; top: 350px; width: 227px; height: 39px;
    border-radius: 20px; background: var(--red); color: var(--white);
    display: flex; align-items: center; justify-content: center;
    font-family: "Montserrat", sans-serif; font-weight: 500; font-size: 13.5px; letter-spacing: .4px;
  }
</style>
</head>
<body>
  <div class="hero-band"></div>
  <div class="hero-photo" role="img" aria-label="Photo: a tutor sitting beside a young student at a sunlit kitchen table, pointing with a pencil at an open workbook"></div>

  <h1 class="headline">Local Tutors. 1-on-1 Learning.</h1>
  <p class="headline-accent">Real Results.</p>

  <form class="lead-form">
    <div class="field col-left row-1"><span class="field-label">STUDENT’S NAME</span></div>
    <div class="field col-right row-1"><span class="field-label">PARENT’S NAME</span></div>
    <div class="field col-left row-2"><span class="field-label">EMAIL ADDRESS</span></div>
    <div class="field col-right row-2"><span class="field-label">PHONE NUMBER</span></div>
    <div class="field col-left row-3"><span class="field-label">GRADE LEVEL</span>
      <svg class="field-caret" style="left:162px" width="9" height="6" viewBox="0 0 9 6"><path d="M0 0h9L4.5 6z" fill="#1a1a1a"/></svg>
    </div>
    <div class="field col-right row-3"><span class="field-label">SUBJECT</span>
      <svg class="field-caret" style="left:159px" width="9" height="6" viewBox="0 0 9 6"><path d="M0 0h9L4.5 6z" fill="#1a1a1a"/></svg>
    </div>
    <div class="field field-message"><span class="field-label">MESSAGE</span></div>
    <div class="submit-button">MATCH ME WITH A TUTOR</div>
  </form>
</body>
</html>
```